Bright Harbor Web Design & Marketing

Will award a 2nd place prize of $100.00 if someone can come up with a logo to match this design!
Updates

Okay, I'm really looking to see some better designs here. What do you think will bring the best designs out? Please remember with all future submissions I'm looking for a cartoon style / illustrator style website. I'm not sure what the technical term is for it, so I uploaded some images in the brief.

Target Market(s)

Small Business Owners

Industry/Entity Type

Marketing

Logo Text

BrightHarbor.com

Number of Pages Required

1 page

Colors

Designer to choose colors to be used in the design.

Requirements
Must have
• Logo should say BrightHarbor.com I would like more than just a text logo. I want some sort of cool custom graphic / icon with it that will look nice on shirts/hats/etc

```html
<!DOCTYPE html>
<html lang="en">
<head>
<meta charset="utf-8">
<title>Bright Harbor Web Design &amp; Marketing</title>
<link rel="stylesheet" href="https://fonts.googleapis.com/css2?family=Cinzel:wght@400;700&family=Ubuntu:wght@400;500;700&family=Tinos:wght@400;700&display=swap">
<style>
:root{
  --teal:#4fc3cf;
  --teal-dark:#2fa7b4;
  --ink:#16161b;
  --night:#1c1c24;
  --grey-btn:#5b5b5b;
  --text:#444;
  --muted:#8a8a8a;
  --blue:#2f6fbf;
  --blue-band:#3b7bc2;
  --orange:#f5a623;
  --red:#d9412b;
  --paper:#f4f2ee;
  --white:#fff;
}
*{box-sizing:border-box;margin:0;padding:0}
html,body{width:1200px;height:4737px;overflow:hidden}
body{position:relative;font-family:'Tinos',serif;color:var(--text);background:var(--white)}
section,header,footer{position:absolute;left:0;width:1200px;overflow:hidden}
.section-title{font-family:'Cinzel',serif;font-weight:700;font-size:34px;letter-spacing:2px;text-align:center;color:#222;text-transform:uppercase}
.section-lead{font-size:14px;line-height:1.45;text-align:center;width:920px;margin:0 auto;color:#555}
.btn{display:inline-flex;align-items:center;gap:8px;font-family:'Ubuntu',sans-serif;font-size:16px;color:#fff;padding:10px 20px;border-radius:3px}
.btn-grey{background:var(--grey-btn)}
.btn-teal{background:var(--teal)}
.placeholder{position:absolute}

/* header */
.site-header{top:0;height:594px;background:var(--teal)}
.top-nav{position:absolute;top:0;left:0;width:1200px;height:70px;background:var(--ink)}
.nav-links{position:absolute;right:140px;top:0;height:70px;display:flex;align-items:center;font-family:'Ubuntu',sans-serif;font-size:15px;color:#fff;text-transform:uppercase}
.nav-links span{padding:0 18px;border-left:1px solid #444;line-height:20px}
.nav-links span:first-child{border:none;color:var(--teal)}
.brand{position:absolute;left:142px;top:0;width:205px;height:150px;background:#fff;display:flex;flex-direction:column;align-items:center;justify-content:center;gap:10px;box-shadow:0 3px 8px rgba(0,0,0,.25);z-index:2}
.brand-mark{width:46px;height:46px;border-radius:50%;background:var(--teal)}
.brand-name{font-family:'Ubuntu',sans-serif;font-weight:700;font-size:21px;color:#222}
.hero-art{left:0;top:70px;width:560px;height:524px;background:radial-gradient(circle at 50% 45%,#6fd0d9,#4fc3cf 70%)}
.hero-title{position:absolute;right:142px;top:208px;width:500px;text-align:right;font-family:'Ubuntu',sans-serif;font-weight:700;font-size:40px;line-height:1.25;color:var(--ink)}
.hero-title .light{color:#fff}
.hero-cta{position:absolute;right:142px;top:458px}
.slider-arrow{position:absolute;top:350px;width:22px;height:28px;background:#222;display:flex;align-items:center;justify-content:center}

/* about */
.about{top:594px;height:328px;background:#fff}
.about .section-title{margin-top:52px}
.about .section-title .brand-word{color:var(--teal);text-transform:none}
.about .section-title small{font-size:16px}
.about .section-lead{margin-top:22px}
.about .section-lead+.section-lead{margin-top:8px}
.about-actions{display:flex;justify-content:center;gap:14px;margin-top:22px}

/* services */
.services{top:922px;height:752px;background:var(--night)}
.services-scene{left:0;top:0;width:1200px;height:752px;background:linear-gradient(180deg,#1b1d26 0%,#262a36 55%,#3a3330 100%)}
.services .section-title{position:relative;color:#fff;margin-top:40px}
.services .section-lead{position:relative;color:#ccc;margin-top:14px}
.service-map{position:absolute;left:0;top:0}
.service-map .label{font-family:'Ubuntu',sans-serif;font-size:14px;font-weight:500;fill:var(--orange)}
.service-map .desc{font-family:'Tinos',serif;font-size:12px;fill:#bbb}
.service-map .num{font-family:'Ubuntu',sans-serif;font-size:14px;font-weight:700;fill:#fff}

/* plans */
.plans{top:1674px;height:663px;background:#fff}
.plans .section-title{margin-top:56px}
.plans-floor{left:0;top:379px;width:1200px;height:284px;background:linear-gradient(180deg,#c99b66,#b07f4c 60%,#9a6c3e)}
.plan-list{position:absolute;top:142px;left:0;width:1200px}
.plan-card{position:absolute;top:0;width:190px;height:458px;background:#fff;border-top:4px solid #444;box-shadow:0 2px 10px rgba(0,0,0,.22);text-align:center}
.plan-icon{width:56px;height:56px;border-radius:50%;margin:26px auto 0;display:flex;align-items:center;justify-content:center}
.plan-name{font-family:'Ubuntu',sans-serif;font-size:17px;color:#222;margin-top:20px}
.plan-price-box{background:#f3f3f3;margin-top:22px;padding:14px 0}
.plan-from{font-size:11px;color:var(--muted)}
.plan-price{font-family:'Ubuntu',sans-serif;font-size:38px;color:#333}
.plan-price sup,.plan-price sub{font-size:13px}
.plan-features{list-style:none;text-align:left;padding:12px 22px;font-size:12px;color:#555}
.plan-features li{padding:6px 0;border-bottom:1px solid #eee}
.plan-features li::before{content:"› ";color:var(--teal)}
.plan-start{display:inline-flex;align-items:center;gap:8px;background:#3a3a3a;color:#fff;font-family:'Ubuntu',sans-serif;font-size:13px;padding:7px 16px;margin-top:8px}
.plan-card.featured .plan-start{background:var(--teal)}
.plan-more{font-size:11px;color:#555;margin-top:6px}

/* video */
.video{top:2337px;height:499px;background:#fff}
.video .section-title{margin-top:72px}
.video-hands{left:330px;top:140px;width:540px;height:360px;background:linear-gradient(90deg,#e6b899,#f1d2bb 20%,transparent 21%,transparent 79%,#f1d2bb 80%,#e6b899)}
.tablet{position:absolute;left:400px;top:120px;width:400px;height:300px;background:#f2f2f2;border:2px solid #d6d6d6;border-radius:22px}
.tablet-screen{position:absolute;left:30px;top:30px;width:336px;height:236px;background:linear-gradient(180deg,#5a64a6,#3c4585);display:flex;align-items:center;justify-content:center}
.play{width:60px;height:60px;border-radius:50%;background:rgba(255,255,255,.9);display:flex;align-items:center;justify-content:center}
.video-link{position:absolute;top:436px;width:1200px;text-align:center;font-family:'Ubuntu',sans-serif;font-size:15px;color:var(--red)}
.video-link span{border-bottom:1px solid var(--red)}

/* band */
.statement{top:2836px;height:101px;background:var(--blue-band);display:flex;align-items:center;justify-content:center}
.statement p{font-family:'Cinzel',serif;font-size:17px;letter-spacing:1px;line-height:1.5;color:#fff;text-align:center;width:900px;text-transform:uppercase}

/* clients */
.clients{top:2937px;height:253px;background:var(--paper)}
.clients .section-title{margin-top:36px}
.clients .section-lead{margin-top:14px}
.client-row{position:absolute;top:170px;left:110px;width:980px;display:flex;align-items:center;justify-content:space-between}
.client{display:flex;align-items:center;gap:7px;font-family:'Ubuntu',sans-serif;font-weight:700;font-size:17px;color:#333}
.client i{display:block;width:13px;height:13px;border-radius:50%;background:#333}
.row-arrow{font-family:'Ubuntu',sans-serif;font-size:26px;color:#999}

/* why */
.why{top:3190px;height:499px}
.why-scene{left:0;top:0;width:1200px;height:499px;background:linear-gradient(180deg,#1e2b1f,#2b3f2a 50%,#1a2419)}
.why .section-title{position:relative;color:#fff;margin-top:48px}
.why .section-lead{position:relative;color:#ccc;margin-top:14px}
.why-figure{left:510px;top:176px;width:180px;height:180px;border-radius:50%;background:radial-gradient(circle,#9a9a9a,#5a6a58 70%,transparent 71%)}
.why-map{position:absolute;left:0;top:0}
.why-map .ft{font-family:'Ubuntu',sans-serif;font-size:14px;font-weight:500;fill:var(--orange)}
.why-map .fd{font-family:'Tinos',serif;font-size:12px;fill:#ddd}

/* team */
.team{top:3689px;height:385px;background:#fff}
.team .section-title{margin-top:50px}
.team .section-lead{margin-top:14px}
.team-row{position:absolute;top:178px;left:142px;width:916px;display:flex;gap:32px}
.member{flex:1;height:136px;border:1px solid #e2e2e2;box-shadow:0 1px 6px rgba(0,0,0,.08);padding:16px 20px;display:grid;grid-template-columns:72px 1fr;column-gap:16px}
.member-photo{width:72px;height:72px;background:linear-gradient(135deg,#b8bcc4,#7d838d)}
.member-name{font-family:'Ubuntu',sans-serif;font-weight:700;font-size:14px;color:#222;text-transform:uppercase;margin-top:14px}
.member-role{font-size:12px;color:var(--teal-dark)}
.member-bio{grid-column:1/3;font-size:12px;color:#666;margin-top:10px;line-height:1.4}
.team-arrow{position:absolute;top:230px;font-family:'Ubuntu',sans-serif;font-size:26px;color:#aaa}

/* inquiry */
.inquiry{top:4074px;height:347px;background:#fff}
.inquiry-photo{left:0;top:0;width:442px;height:347px;background:linear-gradient(120deg,#f6f6f6 0%,#dfe3e8 55%,#c9ced6 100%)}
.inquiry .section-title{position:absolute;left:420px;top:40px;width:360px}
.inquiry-form{position:absolute;left:484px;top:108px;width:528px}
.field-row{display:flex;gap:24px;margin-bottom:12px}
.field{flex:1;height:34px;border:1px solid #e3e3e3;font-size:12px;color:#777;padding:9px 10px}
.field.area{height:72px}
.submit{display:inline-block;background:var(--blue);color:#fff;font-family:'Ubuntu',sans-serif;font-size:13px;padding:8px 22px;margin-top:4px}

/* footer */
.site-footer{top:4421px;height:316px;background:linear-gradient(180deg,#23262d,#15171c)}
.footer-cols{position:absolute;top:30px;left:142px;width:916px;display:grid;grid-template-columns:220px 260px 1fr;gap:40px;color:#ddd;font-size:13px}
.footer-head{font-family:'Ubuntu',sans-serif;font-size:15px;color:#fff;margin-bottom:12px}
.footer-head span{color:var(--orange)}
.footer-links{list-style:none;line-height:1.75}
.footer-links li::before{content:"› ";color:var(--orange)}
.contact-line{display:flex;align-items:center;gap:8px;margin-top:8px}
.contact-line i{display:block;width:16px;height:16px;border-radius:50%;background:var(--blue)}
.news-input{width:210px;height:28px;background:#fff;margin-top:12px;color:#777;font-size:12px;padding:6px 8px}
.news-btn{display:inline-block;background:var(--blue);color:#fff;font-family:'Ubuntu',sans-serif;font-size:13px;padding:6px 16px;margin-top:8px}
.footer-figure{left:900px;top:140px;width:150px;height:110px;background:linear-gradient(180deg,rgba(140,140,140,.35),rgba(90,90,90,.2))}
.footer-bar{position:absolute;left:0;bottom:0;width:1200px;height:38px;background:var(--blue);display:flex;align-items:center;justify-content:space-between;padding:0 142px;color:#fff;font-size:12px}
</style>
</head>
<body>

<header class="site-header">
  <div class="placeholder hero-art" role="img" aria-label="Illustration of a caped cartoon hero flying with a shopping bag"></div>
  <nav class="top-nav">
    <div class="nav-links"><span>Home</span><span>Services &amp; Pricing</span><span>Our Team</span><span>Clients</span><span>Contact Us</span></div>
  </nav>
  <div class="brand"><div class="brand-mark"></div><div class="brand-name">BrightHarbor.com</div></div>
  <h1 class="hero-title">The Design &amp; Marketing Team <span class="light">That Always Puts Honesty &amp; Care</span> Before Profits</h1>
  <div class="hero-cta"><span class="btn btn-grey">
    <svg width="16" height="16" viewBox="0 0 24 24"><path fill="#fff" d="M6.6 10.8a15 15 0 0 0 6.6 6.6l2.2-2.2a1 1 0 0 1 1-.25 11 11 0 0 0 3.6.6 1 1 0 0 1 1 1V20a1 1 0 0 1-1 1A17 17 0 0 1 3 4a1 1 0 0 1 1-1h3.5a1 1 0 0 1 1 1 11 11 0 0 0 .6 3.6 1 1 0 0 1-.25 1z"/></svg>Call Us Today</span></div>
  <div class="slider-arrow" style="left:0"><svg width="10" height="12"><path d="M8 1 2 6l6 5" fill="none" stroke="#fff" stroke-width="2"/></svg></div>
  <div class="slider-arrow" style="right:0"><svg width="10" height="12"><path d="M2 1l6 5-6 5" fill="none" stroke="#fff" stroke-width="2"/></svg></div>
</header>

<section class="about">
  <h2 class="section-title">About <span class="brand-word">BrightHarbor<small>.com</small></span></h2>
  <p class="section-lead">We believe that honesty and integrity come before personal profits. We are a family owned and operated company. Our parents raised us to take care of each other and that is exactly what we have done. We treat each of our clients with the same loyalty and respect that we give each other.</p>
  <p class="section-lead">We are not looking to have hundreds and hundreds of clients. We are looking to expand our family with a handful of like-minded individuals. Companies who take pride in their work and their customers. We want to build mutually beneficial, lucrative, and long term partnerships.</p>
  <div class="about-actions">
    <span class="btn btn-teal"><svg width="14" height="14" viewBox="0 0 24 24"><path d="M5 12h14M13 6l6 6-6 6" fill="none" stroke="#fff" stroke-width="3"/></svg>Read More</span>
    <span class="btn btn-grey"><svg width="14" height="14" viewBox="0 0 24 24"><path fill="#fff" d="M6.6 10.8a15 15 0 0 0 6.6 6.6l2.2-2.2a1 1 0 0 1 1-.25 11 11 0 0 0 3.6.6 1 1 0 0 1 1 1V20a1 1 0 0 1-1 1A17 17 0 0 1 3 4a1 1 0 0 1 1-1h3.5a1 1 0 0 1 1 1 11 11 0 0 0 .6 3.6 1 1 0 0 1-.25 1z"/></svg>Call Us Today</span>
  </div>
</section>

<section class="services">
  <div class="placeholder services-scene" role="img" aria-label="Dark cartoon city street scene with shops and people in the background"></div>
  <h2 class="section-title">Services We Provide</h2>
  <p class="section-lead">Lorem ipsum dolor sit amet, consectetuer adipiscing elit, sed diam nonummy nibh euismod tincidunt ut laoreet dolore magna aliquam erat volutpat. Ut wisi enim ad minim veniam, quis nostrud exerci.</p>
  <svg class="service-map" width="1200" height="752" viewBox="0 0 1200 752">
    <circle cx="600" cy="460" r="215" fill="none" stroke="#6b7a8a" stroke-width="2" stroke-dasharray="6 6"/>
    <circle cx="600" cy="460" r="70" fill="#2a6fb8"/>
    <circle cx="600" cy="460" r="52" fill="none" stroke="#fff" stroke-width="3"/>
    <g>
      <circle cx="526" cy="258" r="38" fill="#f5a623"/><circle cx="550" cy="290" r="13" fill="#222"/><text class="num" x="550" y="295" text-anchor="middle">1</text>
      <text class="label" x="476" y="240" text-anchor="end">Consulting Service</text>
      <text class="desc" x="476" y="258" text-anchor="end">Duis autem vel eum iriure dolor</text>
      <text class="desc" x="476" y="273" text-anchor="end">in hendrerit in vulputate velit</text>
    </g>
    <g>
      <circle cx="674" cy="258" r="38" fill="#28b6d6"/><circle cx="650" cy="290" r="13" fill="#222"/><text class="num" x="650" y="295" text-anchor="middle">2</text>
      <text class="label" x="724" y="240">Website Design &amp; Management</text>
      <text class="desc" x="724" y="258">Duis autem vel eum iriure dolor</text>
      <text class="desc" x="724" y="273">in hendrerit in vulputate velit</text>
    </g>
    <g>
      <circle cx="786" cy="352" r="38" fill="#7dbb3c"/><circle cx="760" cy="380" r="13" fill="#222"/><text class="num" x="760" y="385" text-anchor="middle">3</text>
      <text class="label" x="836" y="334">Logo Design &amp; Branding Materials</text>
      <text class="desc" x="836" y="352">Duis autem vel eum iriure dolor</text>
      <text class="desc" x="836" y="367">in hendrerit in vulputate velit</text>
    </g>
    <g>
      <circle cx="812" cy="497" r="38" fill="#8e44ad"/><circle cx="784" cy="520" r="13" fill="#222"/><text class="num" x="784" y="525" text-anchor="middle">4</text>
      <text class="label" x="862" y="480">Online Store Design &amp; Management</text>
      <text class="desc" x="862" y="498">Duis autem vel eum iriure dolor</text>
      <text class="desc" x="862" y="513">in hendrerit in vulputate velit</text>
    </g>
    <g>
      <circle cx="752" cy="612" r="38" fill="#e0452b"/><circle cx="726" cy="594" r="13" fill="#222"/><text class="num" x="726" y="599" text-anchor="middle">5</text>
      <text class="label" x="802" y="600">Lead Gen Management</text>
      <text class="desc" x="802" y="618">Duis autem vel eum iriure dolor</text>
      <text class="desc" x="802" y="633">in hendrerit in vulputate velit</text>
    </g>
    <g>
      <circle cx="637" cy="672" r="38" fill="#2a6fb8"/><circle cx="612" cy="650" r="13" fill="#222"/><text class="num" x="612" y="655" text-anchor="middle">6</text>
      <text class="label" x="687" y="680">Search Engine Optimization</text>
      <text class="desc" x="687" y="698">Duis autem vel eum iriure dolor</text>
      <text class="desc" x="687" y="713">in hendrerit in vulputate velit</text>
    </g>
    <g>
      <circle cx="462" cy="625" r="38" fill="#27ae8f"/><circle cx="488" cy="604" r="13" fill="#222"/><text class="num" x="488" y="609" text-anchor="middle">7</text>
      <text class="label" x="412" y="612" text-anchor="end">Social Media Marketing</text>
      <text class="desc" x="412" y="630" text-anchor="end">Duis autem vel eum iriure dolor</text>
      <text class="desc" x="412" y="645" text-anchor="end">in hendrerit in vulputate velit</text>
    </g>
    <g>
      <circle cx="388" cy="497" r="38" fill="#f2c12e"/><circle cx="414" cy="520" r="13" fill="#222"/><text class="num" x="414" y="525" text-anchor="middle">8</text>
      <text class="label" x="338" y="480" text-anchor="end">Marketing Material &amp; Print Design</text>
      <text class="desc" x="338" y="498" text-anchor="end">Duis autem vel eum iriure dolor</text>
      <text class="desc" x="338" y="513" text-anchor="end">in hendrerit in vulputate velit</text>
    </g>
    <g>
      <circle cx="414" cy="352" r="38" fill="#1fa3c9"/><circle cx="440" cy="380" r="13" fill="#222"/><text class="num" x="440" y="385" text-anchor="middle">9</text>
      <text class="label" x="364" y="334" text-anchor="end">Crowdsourcing Management</text>
      <text class="desc" x="364" y="352" text-anchor="end">Duis autem vel eum iriure dolor</text>
      <text class="desc" x="364" y="367" text-anchor="end">in hendrerit in vulputate velit</text>
    </g>
  </svg>
</section>

<section class="plans">
  <h2 class="section-title">Select Your Plan</h2>
  <div class="placeholder plans-floor" role="img" aria-label="Warm wooden floorboards"></div>
  <div class="plan-list">
    <div class="plan-card featured" style="left:158px">
      <div class="plan-icon" style="background:#e6f6f8"><svg width="24" height="24" viewBox="0 0 24 24"><circle cx="12" cy="12" r="7" fill="none" stroke="#2fa7b4" stroke-width="2.5"/></svg></div>
      <div class="plan-name">Basic Plan</div>
      <div class="plan-price-box"><div class="plan-from">Starting from</div><div class="plan-price" style="color:var(--teal-dark)"><sup>$</sup>52<sub>.99</sub></div></div>
      <ul class="plan-features"><li>Lorem Ipsum Dolar Iupsm</li><li>Lorem Ipsum Dolar</li><li>Lorem Ipsum Dolar Iupsm</li><li>Lorem Ipsum Dolar</li></ul>
      <span class="plan-start">Get Started →</span><div class="plan-more">More Information</div>
    </div>
    <div class="plan-card" style="left:395px">
      <div class="plan-icon" style="background:#eef0f2"><svg width="24" height="24" viewBox="0 0 24 24"><circle cx="12" cy="12" r="7" fill="none" stroke="#555" stroke-width="2.5"/></svg></div>
      <div class="plan-name">Standard Plan</div>
      <div class="plan-price-box"><div class="plan-from">Starting from</div><div class="plan-price"><sup>$</sup>114<sub>.00</sub></div></div>
      <ul class="plan-features"><li>Lorem Ipsum Dolar Iupsm</li><li>Lorem Ipsum Dolar</li><li>Lorem Ipsum Dolar Iupsm</li><li>Lorem Ipsum Dolar</li></ul>
      <span class="plan-start">Get Started →</span><div class="plan-more">More Information</div>
    </div>
    <div class="plan-card" style="left:625px">
      <div class="plan-icon" style="background:#eef0f2"><svg width="24" height="24" viewBox="0 0 24 24"><circle cx="12" cy="12" r="7" fill="none" stroke="#555" stroke-width="2.5"/></svg></div>
      <div class="plan-name">Gold Plan</div>
      <div class="plan-price-box"><div class="plan-from">Starting from</div><div class="plan-price"><sup>$</sup>200<sub>.99</sub></div></div>
      <ul class="plan-features"><li>Lorem Ipsum Dolar Iupsm</li><li>Lorem Ipsum Dolar</li><li>Lorem Ipsum Dolar Iupsm</li><li>Lorem Ipsum Dolar</li></ul>
      <span class="plan-start">Get Started →</span><div class="plan-more">More Information</div>
    </div>
    <div class="plan-card" style="left:859px">
      <div class="plan-icon" style="background:#eef0f2"><svg width="24" height="24" viewBox="0 0 24 24"><circle cx="10" cy="10" r="6" fill="none" stroke="#555" stroke-width="2.5"/><path d="M14.5 14.5 20 20" stroke="#555" stroke-width="2.5"/></svg></div>
      <div class="plan-name">Platinum Plan</div>
      <div class="plan-price-box"><div class="plan-from">Starting from</div><div class="plan-price"><sup>$</sup>490<sub>.00</sub></div></div>
      <ul class="plan-features"><li>Lorem Ipsum Dolar Iupsm</li><li>Lorem Ipsum Dolar</li><li>Lorem Ipsum Dolar Iupsm</li><li>Lorem Ipsum Dolar</li></ul>
      <span class="plan-start">Get Started →</span><div class="plan-more">More Information</div>
    </div>
  </div>
</section>

<section class="video">
  <h2 class="section-title">Watch Video</h2>
  <div class="placeholder video-hands" role="img" aria-label="Two hands holding a tablet"></div>
  <div class="tablet">
    <div class="tablet-screen"><div class="play"><svg width="22" height="24" viewBox="0 0 22 24"><path d="M4 2l16 10L4 22z" fill="#333"/></svg></div></div>
  </div>
  <div class="video-link"><span>View Video</span></div>
</section>

<section class="statement">
  <p>Lorem ipsum dolor sit amet, consectetuer adipiscing elit, sed diam nonummy nibh euismod tincidunt ut laoreet dolore magna aliquam erat volutpat</p>
</section>

<section class="clients">
  <h2 class="section-title">Our Clients</h2>
  <p class="section-lead">Lorem ipsum dolor sit amet, consectetuer adipiscing elit, sed diam nonummy nibh euismod tincidunt ut laoreet dolore magna aliquam erat volutpat. Ut wisi enim ad minim veniam, quis nostrud exerci.</p>
  <div class="client-row">
    <span class="row-arrow">‹</span>
    <span class="client"><i></i>Marlow</span>
    <span class="client"><i></i>VERITY</span>
    <span class="client"><i></i>VERITY</span>
    <span class="client">Keystone</span>
    <span class="client"><i></i>Marlow</span>
    <span class="client"><i></i>Northwind</span>
    <span class="client">Lumen</span>
    <span class="client">Lumen</span>
    <span class="row-arrow">›</span>
  </div>
</section>

<section class="why">
  <div class="placeholder why-scene" role="img" aria-label="Dark green foliage backdrop"></div>
  <h2 class="section-title">Why Choose Us</h2>
  <p class="section-lead">Lorem ipsum dolor sit amet, consectetuer adipiscing elit, sed diam nonummy nibh euismod tincidunt ut laoreet dolore magna aliquam erat volutpat. Ut wisi enim ad minim veniam, quis nostrud exerci.</p>
  <div class="placeholder why-figure" role="img" aria-label="Illustration of two figures shaking hands"></div>
  <svg class="why-map" width="1200" height="499" viewBox="0 0 1200 499">
    <path d="M330 230 Q600 120 870 230" fill="none" stroke="#6fd0d9" stroke-width="2" stroke-dasharray="5 6"/>
    <path d="M400 320 Q600 470 800 320" fill="none" stroke="#6fd0d9" stroke-width="2" stroke-dasharray="5 6"/>
    <circle cx="400" cy="210" r="22" fill="#2a6fb8"/><circle cx="800" cy="210" r="22" fill="#2a6fb8"/>
    <circle cx="470" cy="318" r="22" fill="#2a6fb8"/><circle cx="730" cy="318" r="22" fill="#2a6fb8"/>
    <circle cx="600" cy="400" r="22" fill="#2a6fb8"/>
    <text class="ft" x="370" y="200" text-anchor="end">100% Risk-Free Investment</text>
    <text class="fd" x="370" y="218" text-anchor="end">Lorem ipsum dolor sit amet, consectetuer</text>
    <text class="fd" x="370" y="233" text-anchor="end">adipiscing elit, sed diam nonummy</text>
    <text class="ft" x="830" y="200">Multiple Payment Options Available</text>
    <text class="fd" x="830" y="218">Lorem ipsum dolor sit amet, consectetuer</text>
    <text class="fd" x="830" y="233">adipiscing elit, sed diam nonummy</text>
    <text class="ft" x="440" y="308" text-anchor="end">Customized Loyalty Program</text>
    <text class="fd" x="440" y="326" text-anchor="end">Lorem ipsum dolor sit amet, consectetuer</text>
    <text class="fd" x="440" y="341" text-anchor="end">adipiscing elit, sed diam nonummy</text>
    <text class="ft" x="760" y="308">Unmatched Personal Service</text>
    <text class="fd" x="760" y="326">Lorem ipsum dolor sit amet, consectetuer</text>
    <text class="fd" x="760" y="341">adipiscing elit, sed diam nonummy</text>
    <text class="ft" x="600" y="442" text-anchor="middle">24/7/365 Customer Support</text>
    <text class="fd" x="600" y="460" text-anchor="middle">Lorem ipsum dolor sit amet, consectetuer</text>
    <text class="fd" x="600" y="475" text-anchor="middle">adipiscing elit, sed diam nonummy</text>
  </svg>
</section>

<section class="team">
  <h2 class="section-title">Our Team</h2>
  <p class="section-lead">Lorem ipsum dolor sit amet, consectetuer adipiscing elit, sed diam nonummy nibh euismod tincidunt ut laoreet dolore magna aliquam erat volutpat. Ut wisi enim ad minim veniam, quis nostrud exerci.</p>
  <span class="team-arrow" style="left:112px">‹</span>
  <span class="team-arrow" style="right:112px">›</span>
  <div class="team-row">
    <div class="member">
      <div class="member-photo" role="img" aria-label="Portrait of Daniel Reyes"></div>
      <div><div class="member-name">Daniel Reyes</div><div class="member-role">Chief Executive Officer</div></div>
      <p class="member-bio">Lorem ipsum dolor sit amet, consectetuer adipiscing elit, sed diam nonummy nibh euismod tincidunt ut laoreet dolore magna aliquam… [+]</p>
    </div>
    <div class="member">
      <div class="member-photo" role="img" aria-label="Portrait of Owen Hale"></div>
      <div><div class="member-name">Owen Hale</div><div class="member-role">Chief Operations Officer</div></div>
      <p class="member-bio">Lorem ipsum dolor sit amet, consectetuer adipiscing elit, sed diam nonummy nibh euismod tincidunt ut laoreet dolore magna aliquam… [+]</p>
    </div>
  </div>
</section>

<section class="inquiry">
  <div class="placeholder inquiry-photo" role="img" aria-label="Hands typing on a laptop at a white desk with a coffee cup"></div>
  <h2 class="section-title">Quick Inquiry</h2>
  <div class="inquiry-form">
    <div class="field-row"><div class="field">First Name</div><div class="field">Last Name</div></div>
    <div class="field-row"><div class="field">Email</div><div class="field">Phone Number</div></div>
    <div class="field-row"><div class="field area">Details About Your Enquiry</div></div>
    <span class="submit">SUBMIT</span>
  </div>
</section>

<footer class="site-footer">
  <div class="placeholder footer-figure" role="img" aria-label="Faint cartoon figures shaking hands"></div>
  <div class="footer-cols">
    <div>
      <div class="footer-head">Quick <span>Links</span></div>
      <ul class="footer-links"><li>Home</li><li>Services</li><li>Pricing</li><li>Our Team</li><li>Success Stories</li><li>Clients</li><li>Contact Us</li></ul>
    </div>
    <div>
      <div class="footer-head">Contact <span>Details</span></div>
      <div style="font-weight:700;color:#fff">BrightHarbor.com</div>
      <div>Street Name, City Name</div>
      <div>State, Zipcode</div>
      <div class="contact-line"><i></i>555-010-4821</div>
      <div class="contact-line"><i></i>555-010-4822</div>
      <div class="contact-line"><i></i>inquiry@brightharbor.com</div>
    </div>
    <div>
      <div class="footer-head">Newsletter <span>Signup</span></div>
      <div>Lorem ipsum dolor sit amet, consectetuer adipiscing elit, sed diam.</div>
      <div class="news-input">Email</div>
      <span class="news-btn">Subscribe</span>
    </div>
  </div>
  <div class="footer-bar"><span>Copyright © 2017 BrightHarbor.com . All rights reserved</span><span>Terms of Use | Privacy Policy</span></div>
</footer>

</body>
</html>
```